Video Learning Web Application Site Design

We are a new company that produce and distribute educational videos using a subscription model on our website. The videos are streamed on our website and users can tailor their own course packages by creating playlists. Each video-lesson are also split into several smaller segments, and it should be easy to find and play those segments.

Please note that both the screenshots and wireframes provided are only how it looks right now, if you as the designer have a better idea on how to present it then please share it.
Updates

Please view the screenshots as well, I believe I forgot to include two buttons on the wireframes that should be on the Our Courses page. Also, there is no need to make a carbon copy of the wireframes/screenshots, I'd like you designers to come up with a better way of displaying the information if possible. For inspiration you can look at sites like ClipHarbor (I like the simplicity of their design) and to some extent the Tessel UI where they divide different areas of the page into clear "zones".

Thanks,

Project Deadline Extended
Reason: I have to extend the deadline because I've been really ill the last week. Will go through the current submissions now and provide feedback and looking forward to more submissions.

Target Market(s)

College and University students. Professionals wanting to expand their knowledge and people that want to learn new skills to get a promotion/new job.

Industry/Entity Type

Tailor

Requirements
Must have
• Must include the logo from the file "brainlark-logo".
• Should include two pages, one of the video-player page and one of the course list.
• Try to incorporate the colors from the logo.
• Please note: If you look at the video-player.png file just below "Åpne Tabell, lage..." there are two rows, those are sub-parts of the lesson. Both these and the main lesson itself must have some easy way to Play and Add to Playlist.
Nice to have
• We prefer flat design, with simple and clean icons. Don't overdo the colors, stay within 3-4 colors with variations of them.
Should not have
• 3D-like elements, lot of shadows or hard to ready text.

```html
<!DOCTYPE html>
<html lang="en">
<head>
<meta charset="utf-8">
<title>brainlark – Our Courses</title>
<link rel="stylesheet" href="https://fonts.googleapis.com/css2?family=PT+Sans:wght@400;700&display=swap">
<style>
:root{
  --blue:#0a86b8;
  --footer:#0781b7;
  --text:#555;
  --muted:#777;
  --line:#dcdcdc;
  --panel:#f4f4f4;
  --btn-top:#8a8a8a;
  --btn-bottom:#5c5c5c;
  --star:#f2c22e;
}
*{box-sizing:border-box;margin:0;padding:0}
html,body{width:1200px;height:871px;overflow:hidden}
body{position:relative;font-family:"PT Sans",sans-serif;color:var(--text);background:#fff;font-size:11px}
.abs{position:absolute}
.header{left:0;top:0;width:1200px;height:74px;background:linear-gradient(#fff,#ececec);border-bottom:1px solid #d6d6d6}
.brand{left:181px;top:16px;display:flex;align-items:center;gap:8px}
.brand-dot{width:34px;height:34px;border-radius:50%;background:var(--blue)}
.brand-name{font-size:36px;font-weight:700;color:var(--blue);line-height:1}
.search{left:406px;top:27px;width:285px;height:24px;border:1px solid #cfcfcf;border-radius:3px;background:#f7f7f7;font-size:9px;padding:6px 12px;color:#666}
.search svg{position:absolute;right:9px;top:5px}
.login{left:720px;width:210px;text-align:right;top:30px;font-size:10.5px;color:#555;white-space:nowrap}
.login span{color:var(--blue)}
.btn{display:flex;align-items:center;justify-content:center;color:#fff;font-weight:700;font-size:10px;border-radius:3px;background:linear-gradient(var(--btn-top),var(--btn-bottom));border:1px solid #4d4d4d}
.logout{left:941px;top:26px;width:78px;height:22px}
.sidebar{left:172px;top:74px;width:210px;height:719px;border-left:1px solid var(--line);border-right:1px solid var(--line)}
.side-head{left:181px;width:192px;height:28px;border:1px solid var(--line);background:linear-gradient(#fff,#f0f0f0);color:var(--blue);font-weight:700;font-size:10.5px;padding:8px 12px}
.side-head i{position:absolute;right:8px;top:6px;width:15px;height:15px;border:1px solid #bbb;border-radius:2px;font-style:normal;color:#888;font-size:11px;line-height:12px;text-align:center;background:#fafafa}
.side-link{left:194px;font-size:10.5px;color:#666}
.side-link::before{content:"»";margin-right:5px;color:#999}
.title{left:405px;top:97px;color:var(--blue);font-weight:700;font-size:14px}
.video{left:405px;top:130px;width:288px;height:205px;border:1px solid #ccc}
.video-frame{width:100%;height:188px;background:linear-gradient(160deg,#6e7a63,#3d3a33 55%,#24221f)}
.play{position:absolute;left:122px;top:72px;width:44px;height:44px;border-radius:50%;background:rgba(0,0,0,.35)}
.play::after{content:"";position:absolute;left:17px;top:13px;border-left:14px solid rgba(255,255,255,.7);border-top:9px solid transparent;border-bottom:9px solid transparent}
.controls{height:16px;background:linear-gradient(#f4f4f4,#d4d4d4);display:flex;align-items:center;font-size:8px;font-weight:700;color:#333;gap:6px;padding:0 6px}
.track{flex:1;height:4px;background:#aaa;border-radius:2px}
.cues{left:722px;top:130px;width:298px;height:205px;border:1px solid var(--line);background:linear-gradient(#efefef,#fff 35%)}
.cues-item{left:16px;top:17px;color:var(--blue);font-weight:700;font-size:10.5px}
.cues-label{left:16px;top:35px;font-size:12.5px;font-weight:700;color:#666}
.cue-list{left:20px;top:62px;width:124px;height:126px;border:1px solid var(--line);background:#fff;list-style:none}
.cue-list li{height:26px;padding:7px 14px;font-size:9.5px;color:#777}
.cue-list li.active{background:#bdbdbd;color:#fff}
.files{left:162px;top:68px}
.files h3{font-size:12px;color:#666;margin-bottom:5px}
.files p{font-size:9.5px;color:#777;margin-bottom:8px}
.files p::before{content:"»";margin-right:5px}
.course-bar{left:407px;top:357px;width:613px;height:44px;background:linear-gradient(#fff,#eee);border-bottom:1px solid var(--line)}
.course-name{left:425px;top:366px;color:var(--blue);font-weight:700;font-size:11px}
.remove{left:551px;top:357px;width:149px;height:29px}
.show-all{left:409px;top:417px;width:124px;height:29px}
.tree-row{display:flex;align-items:center;gap:5px;font-size:9.5px;font-weight:700}
.tree-row.parent{left:410px;color:var(--blue)}
.tree-row.child{left:443px;color:#777}
.tri{width:0;height:0;border-left:5px solid #555;border-top:4px solid transparent;border-bottom:4px solid transparent;margin-right:4px}
.caret{width:0;height:0;border-top:5px solid var(--blue);border-left:4px solid transparent;border-right:4px solid transparent}
.footer{left:0;top:793px;width:1200px;height:78px;background:var(--footer);color:#fff}
.copy{left:183px;top:27px;font-size:9.5px;font-weight:700}
.follow{left:882px;top:29px;font-size:9.5px;font-weight:700}
.social{top:21px;width:26px;height:26px;border-radius:50%}
</style>
</head>
<body>
<header class="abs header"></header>
<div class="abs brand"><span class="brand-dot"></span><span class="brand-name">brainlark</span></div>
<div class="abs search">SEARCH :
  <svg width="16" height="14" viewBox="0 0 16 14"><circle cx="6" cy="6" r="4.5" fill="none" stroke="#999" stroke-width="1.6"/><line x1="9.5" y1="9" x2="14" y2="13" stroke="#999" stroke-width="2.2"/></svg>
</div>
<div class="abs login">Logged in as <span>sam@brainlark.test</span></div>
<div class="abs btn logout">LOGOUT</div>

<aside class="abs sidebar"></aside>
<div class="abs side-head" style="top:91px">INTRODUCTION<i>−</i></div>
<div class="abs side-link" style="top:128px">Introduction</div>
<div class="abs side-head" style="top:154px">MODULES<i>−</i></div>
<div class="abs side-link" style="top:190px">Our Courses</div>
<div class="abs side-link" style="top:208px">Your Courses</div>
<div class="abs side-head" style="top:234px">PLATLISTS<i>+</i></div>
<div class="abs side-link" style="top:271px">My Playlist 1</div>
<div class="abs side-link" style="top:289px">My Playlist 2</div>

<h1 class="abs title">OUR COURSES</h1>
<div class="abs video">
  <div class="video-frame" role="img" aria-label="Video still: students walking up outdoor steps on a campus"></div>
  <div class="play"></div>
  <div class="controls"><span>▶</span><span>00:00</span><span class="track"></span><span>00:00</span><span>◀||||</span><span>⛶</span></div>
</div>

<section class="abs cues">
  <div class="abs cues-item">ITEM 1</div>
  <div class="abs cues-label">Cues</div>
  <ul class="abs cue-list"><li>Child 1</li><li class="active">Child 2</li><li>Child 3</li><li>Child 4</li></ul>
  <div class="abs files"><h3>Files</h3><p>Download Lesson file (As)</p><p>Download Study material</p></div>
</section>

<div class="abs course-bar"></div>
<div class="abs course-name">TABELL 2013 - BEGINNER</div>
<div class="abs btn remove">REMOVE THIS COURSE</div>
<div class="abs btn show-all">SHOW ALL CUES</div>

<svg width="0" height="0" style="position:absolute"><defs><symbol id="star" viewBox="0 0 12 12"><path d="M6 .5l1.6 3.4 3.7.4-2.8 2.5.8 3.7L6 8.6 2.7 10.5l.8-3.7L.7 4.3l3.7-.4z" fill="var(--star)" stroke="#c99a10" stroke-width=".6"/></symbol></defs></svg>

<div class="abs tree-row parent" style="top:463px"><span class="tri"></span><svg width="12" height="12"><use href="#star"/></svg><span class="caret"></span>ITEM 1</div>
<div class="abs tree-row child" style="top:483px"><span class="tri"></span><svg width="12" height="12"><use href="#star"/></svg>Child 1</div>
<div class="abs tree-row child" style="top:503px"><span class="tri"></span><svg width="12" height="12"><use href="#star"/></svg>Child 2</div>
<div class="abs tree-row child" style="top:523px"><span class="tri"></span><svg width="12" height="12"><use href="#star"/></svg>Child 3</div>
<div class="abs tree-row child" style="top:543px"><span class="tri"></span><svg width="12" height="12"><use href="#star"/></svg>Child 4</div>
<div class="abs tree-row parent" style="top:571px"><span class="tri"></span><svg width="12" height="12"><use href="#star"/></svg><span class="caret"></span>ITEM 2</div>
<div class="abs tree-row child" style="top:591px"><span class="tri"></span><svg width="12" height="12"><use href="#star"/></svg>Child 5</div>
<div class="abs tree-row child" style="top:611px"><span class="tri"></span><svg width="12" height="12"><use href="#star"/></svg>Child 6</div>
<div class="abs tree-row child" style="top:631px"><span class="tri"></span><svg width="12" height="12"><use href="#star"/></svg>Child 7</div>
<div class="abs tree-row child" style="top:651px"><span class="tri"></span><svg width="12" height="12"><use href="#star"/></svg>Child 8</div>
<div class="abs tree-row parent" style="top:674px"><span class="tri"></span><svg width="12" height="12"><use href="#star"/></svg><span class="caret"></span>ITEM 3</div>
<div class="abs tree-row child" style="top:695px"><span class="tri"></span><svg width="12" height="12"><use href="#star"/></svg>Child 9</div>
<div class="abs tree-row child" style="top:715px"><span class="tri"></span><svg width="12" height="12"><use href="#star"/></svg>Child 10</div>
<div class="abs tree-row child" style="top:735px"><span class="tri"></span><svg width="12" height="12"><use href="#star"/></svg>Child 11</div>
<div class="abs tree-row child" style="top:755px"><span class="tri"></span><svg width="12" height="12"><use href="#star"/></svg>Child 12</div>

<footer class="abs footer">
  <div class="abs copy">Copyright © 2013. brainlark. All rights reserved.</div>
  <div class="abs follow">Follow Us :</div>
  <span class="abs social" style="left:931px;background:#3a5ea8" aria-label="Social link 1"></span>
  <span class="abs social" style="left:961px;background:#4fb6e6" aria-label="Social link 2"></span>
  <span class="abs social" style="left:991px;background:#2a6f93" aria-label="Social link 3"></span>
</footer>
</body>
</html>
```